Harborline Auto LLC

Car Dealer Customer Service
Address: 2874 Cresthaven Road, Shelbyville, TN 37162
web: www.harborlineautoxq.net
email: harborlineautoxq@mailnest.example
Phone: (931) 555-0148
Phone: (629) 555-0173

```html
<!DOCTYPE html>
<html lang="en">
<head>
<meta charset="UTF-8">
<title>Harborline Auto — Business Card</title>
<link href="https://fonts.googleapis.com/css2?family=Poppins:wght@400;600;700&display=swap" rel="stylesheet">
<style>
  :root {
    --backdrop: #2b2b2c;
    --blue: #1f7bb0;
    --blue-deep: #176a9c;
    --gold: #d9a23a;
    --paper: #f2f2f1;
    --ink: #1c1c1c;
    --white: #ffffff;
  }
  * { box-sizing: border-box; margin: 0; padding: 0; }
  html, body { width: 1200px; height: 1138px; overflow: hidden; }
  body {
    background: var(--backdrop);
    font-family: "Poppins", sans-serif;
    position: relative;
  }
  .card {
    position: absolute;
    border-radius: 16px;
    overflow: hidden;
  }
  /* Front */
  .card-front {
    left: 274px; top: 186px; width: 623px; height: 376px;
    background: linear-gradient(135deg, var(--blue-deep) 0%, var(--blue) 60%, #2486bd 100%);
  }
  .front-disc {
    position: absolute;
    left: -75px; top: 15px;
    width: 350px; height: 350px;
    border-radius: 50%;
    background: var(--white);
  }
  .front-name {
    position: absolute;
    right: 42px; top: 52px;
    color: var(--white);
    font-weight: 700;
    font-size: 29px;
    letter-spacing: 0.5px;
  }
  .front-web {
    position: absolute;
    right: 42px; top: 320px;
    color: var(--white);
    font-size: 14px;
  }
  /* Back */
  .card-back {
    left: 276px; top: 608px; width: 618px; height: 374px;
    background: var(--paper);
  }
  .brand-row {
    position: absolute;
    left: 28px; top: 54px;
    display: flex; align-items: center; gap: 24px;
  }
  .brand-disc {
    width: 100px; height: 100px; border-radius: 50%;
    background: var(--blue);
  }
  .brand-name {
    color: var(--blue);
    font-weight: 700;
    font-size: 36px;
    letter-spacing: 0.5px;
  }
  .person {
    position: absolute; left: 37px; top: 208px;
    color: var(--ink);
  }
  .person-name {
    color: var(--blue-deep);
    font-weight: 700;
    font-size: 21px;
    line-height: 1.2;
  }
  .person-role { font-size: 15px; margin-top: 2px; }
  .person-address { font-size: 15px; line-height: 22px; margin-top: 22px; }
  .contact-list {
    position: absolute; left: 306px; top: 208px;
    list-style: none;
  }
  .contact-list li {
    display: flex; align-items: center; gap: 10px;
    height: 22px; font-size: 15px; color: var(--ink);
  }
  .contact-list li.phone { font-weight: 700; color: var(--blue-deep); font-size: 16px; letter-spacing: 0.5px; }
  .contact-list li.email { font-size: 14px; }
  .contact-list svg { width: 14px; height: 14px; flex: none; }
  .gold-strip {
    position: absolute; left: 0; bottom: 0;
    width: 250px; height: 14px;
    background: var(--gold);
  }
  .footer-band {
    position: absolute; left: 0; bottom: 0;
    width: 618px; height: 44px;
  }
  .footer-text {
    position: absolute; left: 305px; top: 340px;
    color: var(--white);
    font-weight: 600;
    font-size: 15px;
  }
</style>
</head>
<body>
  <section class="card card-front">
    <div class="front-disc"></div>
    <h1 class="front-name">HARBORLINE AUTO</h1>
    <p class="front-web">www.harborlineautoxq.net</p>
  </section>

  <section class="card card-back">
    <div class="brand-row">
      <div class="brand-disc"></div>
      <h2 class="brand-name">HARBORLINE AUTO</h2>
    </div>

    <div class="person">
      <p class="person-name">Darren Holt</p>
      <p class="person-role">Managing Director</p>
      <p class="person-address">2874 Cresthaven Road,<br>Shelbyville, TN 37162</p>
    </div>

    <ul class="contact-list">
      <li class="phone">
        <svg viewBox="0 0 16 16"><path fill="#d9a23a" d="M2 5c0-2 2-3 6-3s6 1 6 3v1h-3V5H5v1H2zM4 7h8l2 6H2z"/><circle cx="8" cy="10" r="1.6" fill="#f2f2f1"/></svg>
        931-555-0148
      </li>
      <li class="phone">
        <svg viewBox="0 0 16 16"><path fill="#d9a23a" d="M2 5c0-2 2-3 6-3s6 1 6 3v1h-3V5H5v1H2zM4 7h8l2 6H2z"/><circle cx="8" cy="10" r="1.6" fill="#f2f2f1"/></svg>
        629-555-0173
      </li>
      <li>
        <svg viewBox="0 0 16 16"><rect x="1" y="3" width="14" height="10" fill="#d9a23a"/><path d="M1 3l7 6 7-6" fill="none" stroke="#f2f2f1" stroke-width="1.4"/></svg>
        www.harborlineautoxq.net
      </li>
      <li class="email">
        <svg viewBox="0 0 16 16"><circle cx="8" cy="8" r="6.5" fill="none" stroke="#d9a23a" stroke-width="1.5"/><ellipse cx="8" cy="8" rx="2.8" ry="6.5" fill="none" stroke="#d9a23a" stroke-width="1.2"/><path d="M1.5 8h13" stroke="#d9a23a" stroke-width="1.2"/></svg>
        harborlineautoxq@mailnest.example
      </li>
    </ul>

    <div class="gold-strip"></div>
    <svg class="footer-band" viewBox="0 0 618 44" preserveAspectRatio="none">
      <path d="M258 0 H618 V44 H234 L246 12 Q251 0 258 0 Z" fill="#1f7bb0"/>
    </svg>
    <p class="footer-text">HARBORLINE AUTO LLC</p>
  </section>
</body>
</html>
```